Visitenkarten/Briefpaier/Kassenkassenbelege für Juwelier
Zielgruppe
Mittelständischer Juwelier mit zwei Filialen. Klassischer Schmuck, Uhren und Modeschmuck
Aufgabenstellung
Es müssen für zwei Geschäfte Visitenkarten, Briefpapier (A4) und Kassenkassenbelege (A6) erstellt werden. Logo und Typo im Anhang. Ein Farbkonzept besteht noch nicht. Die Idee geht in Richtung Bordeaux-Rot.
Generell:
(1) Sieht erstmal nach viel Beschreibung aus, bitte nicht entmutigen lassen, sind zu 90% nur austauschbare Inhalts-/Kontaktdaten.
(2) Für meine Zwecke reicht es vollkommen aus, wenn bei den Vorschlägen zur Arbeitsersparnis erstmal nur mit einer Adresse gearbeitet wird. Wenn ich dann den zutreffenden Designvorschlag gefunden habe, können wir die zweite Adresse in dem ersten Format umsetzen. Ich denke das spart Zeit und Nerven.
(3) Bitte Angaben wie "Tel.:" oder "USt.- ID:" nicht wörtlich nehmen, es soll dabei klar sein worum es geht; wenn "Telefon" ausgeschrieben besser aussieht, bitte in der optisch ansprechenderen Form verwenden.
(4) Bei Fragen, bitte fragen!
(5) Viel Spass bei dem Projekt - Ich freu' mich auf die Vorschläge!
Visitenkarten(1):
Juwelier Brenneck GmbH
www.juwelier-brenneck-beispiel.de
Visitenkarten(2):
Visitenkarten(generell):
(1) Die einzelnen Daten können durch Hervorhebungen wie Adresse, Kontakt, Online/Internet unterteilt bzw. hervorgehoben werden.
(2) Die Visitenkarten sollen farbig gedruckt werden; geplant ist weiß als Hintergrund ist aber nicht zwingend bei einer guten anderen Idee
Briefpapier:
(1)Absender im Adressfeld für DIN-lang Briefumschläge mit Fenster:
(2)Informationen im Footer/Seitenbereich:
Juwelier Brenneck Gmb..

```html
<!DOCTYPE html>
<html lang="de">
<head>
<meta charset="utf-8">
<title>Juwelier Brenneck – Visitenkarte</title>
<link rel="stylesheet" href="https://fonts.googleapis.com/css2?family=Open+Sans:wght@400;600;700&display=swap">
<style>
  :root {
    --bg: #e6e7e7;
    --card-white: #fbfbfb;
    --sage: #89a29c;
    --slate: #858585;
    --ink: #6f6f6f;
    --line: #c9d3d0;
    --white: #ffffff;
  }
  * { box-sizing: border-box; margin: 0; padding: 0; }
  html, body { width: 1200px; height: 800px; overflow: hidden; }
  body {
    background: var(--bg);
    font-family: "Open Sans", Arial, sans-serif;
    display: flex;
    align-items: center;
    justify-content: center;
    gap: 60px;
  }
  .card {
    position: relative;
    width: 510px;
    height: 330px;
    overflow: hidden;
  }
  /* Front side */
  .card--front { background: var(--sage); }
  .front__mark {
    position: absolute;
    left: 120px; top: 70px;
    width: 64px; height: 64px;
    background: var(--white);
  }
  .front__name {
    position: absolute;
    left: 120px; top: 150px;
    color: var(--white);
    font-weight: 600;
    font-size: 30px;
    letter-spacing: 3px;
    text-transform: uppercase;
  }
  .front__rule {
    position: absolute;
    left: 120px; top: 200px;
    width: 290px; height: 1px;
    background: var(--line);
  }
  .front__tab {
    position: absolute;
    right: 0; bottom: 50px;
    width: 38px; height: 34px;
    background: var(--slate);
  }
  /* Back side */
  .card--back { background: var(--card-white); }
  .back__tab-top {
    position: absolute;
    left: 70px; top: 0;
    width: 48px; height: 42px;
    background: var(--slate);
  }
  .back__tab-side {
    position: absolute;
    right: 0; bottom: 60px;
    width: 34px; height: 34px;
    background: var(--slate);
  }
  .back__contact {
    position: absolute;
    left: 70px; top: 120px;
    font-size: 15px;
    line-height: 1.6;
    color: var(--sage);
  }
  .back__company {
    color: var(--ink);
    font-weight: 700;
    font-size: 16px;
    text-transform: uppercase;
    letter-spacing: 0.5px;
  }
  .label { color: var(--ink); font-weight: 700; }
  .web { color: var(--ink); font-weight: 600; }
</style>
</head>
<body>
  <section class="card card--front" aria-label="Vorderseite Visitenkarte">
    <div class="front__mark"></div>
    <p class="front__name">Juwelier Brenneck</p>
    <div class="front__rule"></div>
    <div class="front__tab"></div>
  </section>

  <section class="card card--back" aria-label="Rückseite Visitenkarte">
    <div class="back__tab-top"></div>
    <div class="back__contact">
      <p class="back__company">Juwelier Brenneck GmbH</p>
      <p>Lindenallee 12 in 45100 Musterstadt a.d. Ruhr</p>
      <p><span class="label">TEL</span> 0200-123450 &nbsp;<span class="label">FAX</span> 0200-123459 &nbsp;</p>
      <p><span class="label">info@juwelier-brenneck-beispiel.de</span></p>
      <p class="web">www.juwelier-brenneck-beispiel.de</p>
    </div>
    <div class="back__tab-side"></div>
  </section>
</body>
</html>
```